Construction company business card

One side to be the logo with the company name, The other side I would like: (Tomas verbick) Project manager 41 barrow crescent kelmore 52917306224783(03) 9703 2428Info@gudeljgroup.comAnd then maybe a couple dot points saying what we do:Construction (commercial & industrial) Civil construction

Anything else please contact me!
Maybe curved st one edge of the card

Target Market(s)

Older clientele

Industry/Entity Type

Construction Company

Contact Information for Business Card

Read above

Colors
3277b5
1b1b1b
9d9d9d

Requirements
Must have
• Use my logo on one side
Nice to have
• Read above
Should not have
• Read above

```html
<!DOCTYPE html>
<html lang="en">
<head>
<meta charset="utf-8">
<title>Strongform Property Group – Business Card</title>
<link rel="stylesheet" href="https://fonts.googleapis.com/css2?family=Open+Sans:wght@400;600;700&display=swap">
<style>
  :root {
    --brand-blue: #3277b5;
    --card-black: #1b1b1b;
    --steel-grey: #9d9d9d;
    --text-light: #d9d9d9;
    --backdrop: #141414;
    --front-top: #3a4d5c;
    --front-bottom: #1c2a35;
  }
  * { box-sizing: border-box; margin: 0; padding: 0; }
  html, body {
    width: 1200px; height: 900px; overflow: hidden;
    background: var(--backdrop);
    font-family: "Open Sans", Arial, sans-serif;
  }
  .canvas { position: relative; width: 1200px; height: 900px; }
  .card {
    position: absolute;
    width: 600px; height: 343px;
    border-radius: 26px;
    overflow: hidden;
    box-shadow: 0 18px 40px rgba(0,0,0,0.6);
  }
  /* Front side */
  .card--front { left: 110px; top: 100px; }
  .front-backdrop {
    position: absolute; inset: 0;
    background: linear-gradient(160deg, var(--front-top) 0%, #2b3b48 45%, var(--front-bottom) 100%);
  }
  .front-brand {
    position: absolute; left: 0; right: 0; top: 88px;
    display: flex; align-items: center; justify-content: center; gap: 16px;
  }
  .brand-dot {
    width: 54px; height: 54px; border-radius: 50%;
    background: var(--brand-blue);
    flex: none;
  }
  .brand-name {
    font-weight: 700; font-size: 30px; line-height: 1.05;
    color: var(--brand-blue); text-transform: uppercase; letter-spacing: 1px;
  }
  .services {
    position: absolute; left: 34px; right: 34px; bottom: 40px;
    display: flex; gap: 22px; list-style: none;
    font-size: 17px; color: #ffffff;
  }
  .services li { display: flex; align-items: center; gap: 7px; }
  .services li::before {
    content: ""; width: 8px; height: 8px; border-radius: 50%;
    background: var(--brand-blue);
  }
  /* Back side */
  .card--back { left: 490px; top: 460px; background: var(--card-black); }
  .back-brand {
    position: absolute; left: 30px; top: 0; bottom: 0; width: 250px;
    display: flex; flex-direction: column; align-items: center; justify-content: center; gap: 14px;
  }
  .back-brand .brand-dot { width: 90px; height: 90px; }
  .back-brand .brand-name { font-size: 27px; text-align: center; }
  .divider {
    position: absolute; left: 300px; top: 30px; bottom: 30px; width: 1px;
    background: linear-gradient(to bottom, transparent, #4a4a4a 20%, #4a4a4a 80%, transparent);
  }
  .contact {
    position: absolute; left: 325px; top: 62px; right: 20px;
    color: var(--text-light); font-size: 16px; line-height: 1.45;
  }
  .contact-name {
    color: var(--brand-blue); font-weight: 600; font-size: 21px;
    text-transform: uppercase; line-height: 1.2;
  }
  .contact-role { margin-bottom: 8px; }
  .contact-address { font-style: normal; margin-bottom: 8px; }
  .contact-lines { list-style: none; }
  .contact-lines li { display: flex; align-items: center; gap: 8px; }
  .contact-lines svg { width: 14px; height: 14px; fill: var(--brand-blue); flex: none; }
</style>
</head>
<body>
<main class="canvas">

  <section class="card card--front" aria-label="Card front">
    <div class="front-backdrop" role="img" aria-label="Soft blurred office interior in slate blue tones"></div>
    <div class="front-brand">
      <span class="brand-dot"></span>
      <span class="brand-name">Strongform<br>Property Group</span>
    </div>
    <ul class="services">
      <li>Construction (commercial &amp; industrial)</li>
      <li>Civil construction</li>
    </ul>
  </section>

  <section class="card card--back" aria-label="Card back">
    <div class="back-brand">
      <span class="brand-dot"></span>
      <span class="brand-name">Strongform<br>Property Group</span>
    </div>
    <div class="divider"></div>
    <div class="contact">
      <p class="contact-name">Tomas Verbick</p>
      <p class="contact-role">Project manager</p>
      <address class="contact-address">41 barrow crescent<br>kelmore 5291</address>
      <ul class="contact-lines">
        <li>
          <svg viewBox="0 0 16 16" aria-hidden="true"><path d="M3 6c0-2 2-3 5-3s5 1 5 3l-2 1-1-2H6L5 7 3 6zm1 2h8l1 5H3l1-5zm4 1a1.5 1.5 0 100 3 1.5 1.5 0 000-3z"/></svg>
          7306224783
        </li>
        <li>
          <svg viewBox="0 0 16 16" aria-hidden="true"><path d="M5 1h6a1 1 0 011 1v12a1 1 0 01-1 1H5a1 1 0 01-1-1V2a1 1 0 011-1zm1 2v9h4V3H6zm2 10a.8.8 0 100 1.6.8.8 0 000-1.6z"/></svg>
          (03) 9418 6573
        </li>
        <li>
          <svg viewBox="0 0 16 16" aria-hidden="true"><path d="M1 4h14v9H1V4zm1 1v.4l6 4 6-4V5H2zm0 1.6V12h12V6.6L8 10.6 2 6.6z"/></svg>
          Info@verbickgroup.com
        </li>
      </ul>
    </div>
  </section>

</main>
</body>
</html>
```